Locksmith Business Cards

My father-in-law is in need of new business cards for his locksmith business and I need to impress him. Kindly help me out!

You can see the previous business card attached. It is a family run business in North Wales.

No individual names on the cards.

Key Things to Feature:
- The words "Prompt", "Local", "Reliable" (as you can see under the logo on the website)
- 24h Emergency Service
- Covering All of North Wales, the Wirral and Chester
- The color blue
- A key or a lock would be interesting (similar to the ones that come up when you google locksmith business card)

Optional (only if design includes bullet points, like the example below):
https://imgvaultcdn.net/samples/208314/55172/55172_3904821_208314_image.jpg
- Residential / Commercial / Automotive
- Alarms & Cameras
- Key Cutting & Safes

https://www.brynhafod-locksmiths.co.uk/

Industry/Entity Type

Locksmith

Contact Information for Business Card

01632 960 418
07700 900 362
brynhafodlocksmiths@mailvane.com
Brynhafod Locksmiths, The Willow Barn, 7 Tannery Rd., Llandudno LL99 4QX
www.brynhafod-locksmiths.co.uk

Requirements
Must have
• - The words "Prompt", "Local", "Reliable" (as you can see under the logo on the website)
• - 24h Emergency Service
• - Covering All of North Wales, the Wirral and Chester
Nice to have
• - A key or a lock would be interesting (similar to the ones that come up when you google locksmith business card)

```html
<!DOCTYPE html>
<html lang="en">
<head>
<meta charset="utf-8">
<title>Brynhafod Locksmiths – Business Card</title>
<link rel="stylesheet" href="https://fonts.googleapis.com/css2?family=Open+Sans:wght@400;600;700&family=Oswald:wght@500;600&display=swap">
<style>
  :root {
    --navy: #1f2a63;
    --mid-blue: #4a5da8;
    --paper: #ffffff;
    --ink-grey: #555a66;
    --backdrop: #e9eaee;
  }
  * { box-sizing: border-box; margin: 0; padding: 0; }
  html, body { width: 1200px; height: 900px; overflow: hidden; background: var(--backdrop); }
  .canvas { position: relative; width: 1200px; height: 900px; }

  .card {
    position: absolute; width: 620px; height: 400px; overflow: hidden;
    box-shadow: 0 6px 18px rgba(0,0,0,.18);
  }

  /* Back side */
  .card-back { left: 80px; top: 50px; background: var(--navy); color: var(--paper); }
  .back-name {
    position: absolute; left: 50px; top: 145px; width: 200px;
    font-family: "Oswald", sans-serif; font-weight: 600; font-size: 34px;
    line-height: 1.1; text-transform: uppercase; color: var(--paper);
  }
  .back-divider { position: absolute; left: 270px; top: 120px; width: 1px; height: 160px; background: rgba(255,255,255,.35); }
  .service-list {
    position: absolute; left: 290px; top: 150px; list-style: none;
    font-family: "Oswald", sans-serif; font-weight: 500; font-size: 19px; line-height: 1.45;
  }
  .service-list li::before {
    content: ""; display: inline-block; width: 8px; height: 8px; border-radius: 50%;
    background: var(--paper); margin-right: 8px; vertical-align: middle;
  }

  /* Front side */
  .card-front { left: 500px; top: 470px; background: var(--paper); }
  .address {
    position: absolute; left: 50px; top: 50px;
    font-family: "Open Sans", sans-serif; font-size: 17px; line-height: 1.3; color: var(--ink-grey);
  }
  .brand { position: absolute; right: 40px; top: 55px; text-align: right; }
  .brand-name {
    font-family: "Oswald", sans-serif; font-weight: 600; font-size: 28px; line-height: 1.05;
    text-transform: uppercase; color: var(--navy);
  }
  .brand-tagline {
    margin-top: 4px; font-family: "Oswald", sans-serif; font-weight: 600; font-size: 15px; color: var(--navy);
  }
  .contact-list {
    position: absolute; left: 95px; top: 186px; list-style: none;
    font-family: "Open Sans", sans-serif; font-size: 17px; line-height: 24px; color: var(--navy);
  }
  .contact-list li { display: flex; align-items: center; gap: 9px; }
  .contact-list svg { width: 14px; height: 14px; fill: var(--navy); flex: none; }

  .wave { position: absolute; left: 0; top: 0; width: 620px; height: 400px; }
  .emergency {
    position: absolute; right: 22px; top: 302px;
    font-family: "Open Sans", sans-serif; font-weight: 700; font-size: 15px; color: var(--paper);
  }
  .coverage {
    position: absolute; right: 22px; top: 352px;
    font-family: "Open Sans", sans-serif; font-size: 17px; color: var(--paper);
  }
</style>
</head>
<body>
<main class="canvas">

  <section class="card card-back" aria-label="Business card, back">
    <div class="back-name">Brynhafod Locksmiths</div>
    <div class="back-divider"></div>
    <ul class="service-list">
      <li>Residential / Commercial / Automotive</li>
      <li>Alarms &amp; Cameras</li>
      <li>Key Cutting &amp; Safes</li>
    </ul>
  </section>

  <section class="card card-front" aria-label="Business card, front">
    <svg class="wave" viewBox="0 0 620 400" aria-hidden="true">
      <path fill="var(--mid-blue)" d="M0,290 C160,380 390,320 620,175 L620,400 L0,400 Z"/>
      <path fill="var(--paper)" d="M0,302 C160,390 390,332 620,192 L620,400 L0,400 Z"/>
      <path fill="var(--navy)" d="M0,308 C160,395 390,338 620,198 L620,400 L0,400 Z"/>
    </svg>

    <p class="address">Brynhafod Locksmiths,<br>The Willow Barn, 7,<br>Tannery Rd., Llandudno LL99 4QX</p>

    <div class="brand">
      <div class="brand-name">Brynhafod<br>Locksmiths</div>
      <div class="brand-tagline">Prompt. Local. Reliable</div>
    </div>

    <ul class="contact-list">
      <li><svg viewBox="0 0 16 16"><path d="M3 2h3l1.5 3.5-2 1.2a8 8 0 0 0 3.8 3.8l1.2-2L14 10v3a1 1 0 0 1-1 1A11 11 0 0 1 2 3a1 1 0 0 1 1-1z"/></svg>01632 960 418</li>
      <li><svg viewBox="0 0 16 16"><path d="M4.5 0h7A1.5 1.5 0 0 1 13 1.5v13a1.5 1.5 0 0 1-1.5 1.5h-7A1.5 1.5 0 0 1 3 14.5v-13A1.5 1.5 0 0 1 4.5 0zM5 2v10h6V2zm3 11a1 1 0 1 0 0 2 1 1 0 0 0 0-2z"/></svg>07700 900 362</li>
      <li><svg viewBox="0 0 16 16"><path d="M1 3h14v10H1zm1.5 1.5v.3L8 9l5.5-4.2v-.3z"/></svg>brynhafodlocksmiths@mailvane.com</li>
      <li><svg viewBox="0 0 16 16"><circle cx="8" cy="8" r="7"/></svg>www.brynhafod-locksmiths.co.uk</li>
    </ul>

    <div class="emergency">24H EMERGENCY SERVICE</div>
    <div class="coverage">Covering All of North Wales, the Wirral and Chester</div>
  </section>

</main>
</body>
</html>
```